Animation College website

Name of College: Brightloom Academy of 3D Animation and VFX

We need a redesigned modern website for Brightloom. The web-design should communicate a VFX and animation school and education. We will also need full access to the website once completed. We will also need access to the website to be able to make changes to the content and site ideally the website would be built on Wordpress.

To learn more about what the College please visit: http://brightloom-academy.example/
The video on the homepage demonstrates why Brightloom is a unique college offering 3D animation and VFX. The direct link to the video can be watched here: https://videohost.example/482915036

Client Profile Summary: Brightloom is an improved concept in job skills training for the 3D animation and visual effects industries. Our high graduate job placement numbers are based on the assertion that job skills must include more than simply learning to use software tools. Where nearly every digital media program teaches tools, job skills training should be about learning how to do a job in addition to learning how to use software tools. Brightloom is taught in an apprenticeship style with very experienced faculty mentoring and teaching students to learn how to master their craft (VFX and animation) so they can seamlessly step into industry and excel.

Target Market(s)

High school students, students interested in learning about animation and 3D.

Industry/Entity Type

College

Coding

Coded - Design and coding required

Number of Pages Required

5+ page

Font styles to use
Sans Serif

Colors

Designer to choose colors to be used in the design.

Requirements
Must have
• Please include the video on the current Brightloom-academy.example website. https://videohost.example/482915036
• Use the same content on the current brightloom-academy.example website.
• Include a page to showcase student work.
• Website must also be mobile responsive.
Should not have
• The attached PDF of the landing page is just an example of something we like. You do not have to replicate this. The PDF landing page is showing the colour blue you should incorporate.

```html
<!DOCTYPE html>
<html lang="en">
<head>
<meta charset="utf-8">
<title>Brightloom Academy of 3D Animation and VFX</title>
<link rel="stylesheet" href="https://fonts.googleapis.com/css2?family=Roboto:ital,wght@0,400;0,500;0,700;1,400;1,500&family=Open+Sans:wght@400;600&display=swap">
<style>
:root{
  --blue:#1f6fb8;
  --blue-deep:#17599a;
  --blue-title:#1a5ea8;
  --ink:#222;
  --body:#555;
  --panel:#2b2b2b;
  --footer:#3a3a3a;
  --yellow:#f2c230;
  --white:#fff;
}
*{box-sizing:border-box;margin:0;padding:0}
html,body{width:1200px;height:3066px;overflow:hidden}
body{font-family:"Open Sans",Arial,sans-serif;color:var(--body);background:var(--white);position:relative}
.wrap{width:934px;margin-left:133px}

/* hero */
.hero{position:relative;height:597px;background:linear-gradient(160deg,#3b3d3a 0%,#1e2022 45%,#2c2a24 70%,#141414 100%)}
.hero-photo{position:absolute;inset:0;background:radial-gradient(ellipse at 55% 35%,rgba(120,140,160,.35),transparent 55%),radial-gradient(ellipse at 20% 70%,rgba(90,70,40,.35),transparent 60%)}
.brand{position:absolute;left:130px;top:26px;display:flex;align-items:center;gap:14px;color:var(--white);font-family:"Roboto",sans-serif}
.brand-mark{width:52px;height:52px;background:var(--white)}
.brand-name{font-size:30px;font-weight:500;line-height:1}
.brand-sub{font-size:13px;font-weight:500;margin-top:4px}
.hero-title{position:absolute;left:133px;top:340px;color:var(--white);font-family:"Roboto",sans-serif;font-weight:700;font-size:22px}
.hero-tag{position:absolute;left:133px;top:374px;color:var(--yellow);font-size:12px}

.partners{height:143px;background:var(--blue-deep);position:relative}
.partner{position:absolute;top:32px;width:76px;height:76px;border-radius:50%;background:rgba(255,255,255,.9)}
.partner.square{border-radius:6px;width:64px;height:64px;top:38px}

/* form */
.enquiry{position:absolute;left:711px;top:104px;width:356px;height:593px;background:var(--panel);z-index:2}
.enquiry-head{height:68px;background:var(--blue);color:var(--white);font-family:"Roboto",sans-serif;font-size:23px;display:flex;align-items:center;justify-content:center}
.enquiry-intro{color:var(--white);font-size:12px;text-align:center;line-height:17px;margin:20px 30px 17px}
.field{display:block;width:323px;height:47px;margin:0 0 4px 17px;background:var(--white);border:1px solid #ddd;font-size:12px;color:#555;padding:14px 10px}
.field.comments{height:106px}
.send{display:flex;align-items:center;justify-content:center;width:317px;height:54px;margin:14px 0 0 19px;background:var(--blue);color:var(--white);font-family:"Roboto",sans-serif;font-size:17px}

/* content sections */
.section h2{font-family:"Roboto",sans-serif;font-weight:400;font-size:28px;color:var(--ink)}
.section .lead{font-family:"Roboto",sans-serif;font-style:italic;font-weight:500;font-size:18px;color:var(--blue-title);margin:10px 0 18px}
.section p{font-size:11px;line-height:19px;margin-bottom:16px}
.intro{height:286px;padding-top:42px}
.media{height:462px;background:linear-gradient(180deg,#3c4248 0%,#5b6670 40%,#7c8a92 65%,#2f3a40 100%);position:relative}
.video{position:absolute;left:343px;top:78px;width:514px;height:308px;background:linear-gradient(100deg,#4a3a6a 0%,#6a4c7a 30%,#8a2f2a 65%,#1a1414 100%)}
.play{position:absolute;left:50%;top:50%;transform:translate(-50%,-50%)}
.experts{height:384px;padding-top:60px}
ol.steps{list-style:none;counter-reset:s;font-size:14px;line-height:24px}
ol.steps li{counter-increment:s}
ol.steps li::before{content:counter(s) ". ";color:var(--blue)}
.testimonial{height:532px;position:relative;background:linear-gradient(180deg,#5a2a14 0%,#c85a1c 35%,#d8722a 55%,#4a2416 100%)}
.quote-box{position:absolute;left:282px;top:176px;width:642px;height:286px;background:rgba(31,111,184,.92);padding:8px}
.quote-inner{border:1px solid rgba(255,255,255,.7);height:100%;padding:54px 56px 0 56px;color:var(--white);font-size:12px;line-height:25px}
.quote-name{text-align:right;margin-top:18px;line-height:22px}
.avatar{position:absolute;left:529px;top:88px;width:140px;height:140px;border-radius:50%;border:5px solid #ddd;background:linear-gradient(160deg,#e8c6a4,#b07e58)}
.advantage{height:462px;padding-top:60px}
ul.ticks{list-style:none;font-size:14px;line-height:24.5px}
ul.ticks li::before{content:"\00BB  ";color:var(--blue);font-weight:600}
.cta{height:139px;background:var(--blue-deep);text-align:center;color:var(--white);font-family:"Roboto",sans-serif;padding-top:38px}
.cta h3{font-weight:400;font-size:27px}
.cta p{font-style:italic;font-weight:500;font-size:18px;margin-top:12px}
.footer{height:61px;background:var(--footer);color:#bbb;font-size:11px;display:flex;align-items:center;justify-content:space-between;padding:0 133px 0 133px}
.social{display:flex;gap:18px}
.social span{width:16px;height:16px;border-radius:50%;background:#ddd;display:block}
</style>
</head>
<body>

<header class="hero">
  <div class="hero-photo" role="img" aria-label="Student working at a 3D animation workstation"></div>
  <div class="brand">
    <span class="brand-mark"></span>
    <div><div class="brand-name">Brightloom</div><div class="brand-sub">School of 3D Animation &amp; VFX</div></div>
  </div>
  <h1 class="hero-title">3D Aniation &amp; VFX One-year Intensive Trainning program</h1>
  <p class="hero-tag">Train alongsidepassionate and experienced industry masters</p>
</header>

<div class="partners">
  <span class="partner" style="left:126px"></span>
  <span class="partner" style="left:222px"></span>
  <span class="partner" style="left:344px"></span>
  <span class="partner square" style="left:466px"></span>
  <span class="partner square" style="left:606px"></span>
</div>

<form class="enquiry">
  <div class="enquiry-head">WANT TO KNOW MORE?</div>
  <p class="enquiry-intro">Complete this form to receive more<br>information about program details &amp; more!</p>
  <span class="field">First name</span>
  <span class="field">Last Name</span>
  <span class="field">Phone</span>
  <span class="field">Email</span>
  <span class="field">Country of Residence</span>
  <span class="field comments">Comments</span>
  <span class="send">SEND ME FREE INFO</span>
</form>

<section class="section intro">
  <div class="wrap">
    <h2>One- Year Intensive Training program</h2>
    <p class="lead">An exciting, comprehensive program with a 100% graduate employment rate</p>
    <p>Lorem ipsum dolor sit amet, consectetur adipiscing elit, sed do eiusmod tempor incididunt ut labore et dolore magna aliqua. Ut enim ad minim veniam, quis nostrud exercitation ullamco laboris nisi ut aliquip ex ea commodo consequat. Duis aute irure dolor in reprehenderit in voluptate velit esse cillum dolore eu fugiat nulla pariatur. Excepteur sint occaecat cupidatat non proident, sunt in culpa qui officia deserunt mollit anim id est laborum. Sed ut perspiciatis unde omnis iste natus error sit voluptatem accusantium doloremque laudantium, totam rem aperiam, eaque ipsa quae ab illo inventore veritatis et quasi architecto beatae vitae dicta sunt explicabo. Nemo enim ipsam voluptatem quia voluptas sit aspernatur aut odit aut fugit, sed quia consequuntur magni dolores eos qui ratione voluptatem sequi nesciunt.</p>
  </div>
</section>

<section class="media" role="img" aria-label="Stormy sea backdrop">
  <div class="video" role="img" aria-label="Video still of a student at an editing workstation">
    <svg class="play" width="68" height="68" viewBox="0 0 68 68"><circle cx="34" cy="34" r="31" fill="none" stroke="#fff" stroke-width="3"/><path d="M27 21 L48 34 L27 47 Z" fill="#fff"/></svg>
  </div>
</section>

<section class="section experts">
  <div class="wrap">
    <h2>Learn Animation &amp; Visual Effects production from the Experts</h2>
    <p class="lead">The world's first and sole siulated prodcution training program</p>
    <p>Lorem ipsum dolor sit amet, consectetur adipiscing elit, sed do eiusmod tempor incididunt ut labore et dolore magna aliqua. Ut enim ad minim veniam, quis nostrud exercitation ullamco laboris nisi ut aliquip ex ea commodo consequat. Duis aute irure dolor in reprehenderit in voluptate velit esse cillum dolore eu fugiat nulla pariatur.</p>
    <p>&nbsp;Excepteur sint occaecat cupidatat non proident, sunt in culpa qui officia deserunt mollit anim id est laborum.</p>
    <ol class="steps">
      <li>Sed ut perspiciatis unde omnis iste natus error sit voluptatem accusantium doloremque laudantium, totam rem aperiam</li>
      <li>Neque porro quisquam est, qui dolorem ipsum quia dolor sit amet, consectetur</li>
      <li>Ut enim ad minima veniam, quis nostrum exercitationem</li>
    </ol>
  </div>
</section>

<section class="testimonial" role="img" aria-label="Ruined city under an orange sky">
  <div class="avatar" role="img" aria-label="Portrait of the graduate"></div>
  <div class="quote-box">
    <div class="quote-inner">
      <p>Lorem ipsum dolor sit amet, consectetur adipiscing elit, sed do eiusmod tempor incididunt ut labore et dolore magna aliqua. Ut enim ad minim veniam, quis nostrud exercitation ullamco laboris nisi ut aliquip ex ea commodo consequat. Duis aute irure dolor in reprehenderit in voluptate velit esse cillum dolore eu fugiat nulla pariatur.</p>
      <p class="quote-name">John Doe<br>Lighting Artist Graduate</p>
    </div>
  </div>
</section>

<section class="section advantage">
  <div class="wrap">
    <h2>The Brightloom Advantage</h2>
    <p class="lead">A progra designed by industry, for industry</p>
    <p>Lorem ipsum dolor sit amet, consectetur adipiscing elit, sed do eiusmod tempor incididunt ut labore et dolore magna aliqua. Ut enim ad minim veniam, quis nostrud exercitation ullamco laboris nisi ut aliquip ex ea commodo consequat. Duis aute irure dolor in reprehenderit in voluptate velit esse cillum dolore eu fugiat nulla pariatur.</p>
    <p>&nbsp;Excepteur sint occaecat cupidatat non proident, sunt in culpa qui officia deserunt mollit anim id est laborum.</p>
    <ul class="ticks">
      <li>Sed ut perspiciatis unde omnis iste natus error sit</li>
      <li>Neque porro quisquam est, qui dolorem</li>
      <li>Ut enim ad minima veniam</li>
      <li>Excepteur sint occaecat cupidatat</li>
      <li>Neque porro quisquam</li>
      <li>Ut enim ad minima veniam</li>
      <li>Excepteur sint occaecat cupidatat</li>
    </ul>
  </div>
</section>

<section class="cta">
  <h3>Want to Learn More?</h3>
  <p>Fill out the Form Above To Receive Information about the program!</p>
</section>

<footer class="footer">
  <span>2017 © brightloom-academy.example. All right reserved.</span>
  <div class="social"><span></span><span></span><span></span><span></span><span></span><span></span></div>
</footer>

</body>
</html>
```